Valdane Companies Business Card Design

We need a new business card for our Private Equity Real Estate Development firm, “Valdane” and our EB-5 regional center “Thornmere Regional Center” on one card. We prefer a design that is simple, elegant, and represents the luxury products we design and build as well as the financial security and stability our successful history has produced. We are an industry leader in our field and 3rd generation family business that has evolved into an institutional quality investment platform. Considered design size is standard business card dimensions (3.5 x 2 inches with an additional 1/8 inch space for design elements or backgrounds that extend beyond the finished size of your piece.

Target Market(s)

• High net worth individuals
• Highly skilled technical workers and physicians in the US seeking investment-based immigration opportunities
• Sophisticated private equity investors
• Intermediary partners include domestic attorneys and investment brokers, as well as international agent networks
• US real estate developers

Industry/Entity Type

Finance

Contact Information for Business Card

(Providing placeholder info for personal information, please design for longer character spaces, longer names and addresses etc..)
• Logo for Valdane
• Logo for Thornmere Regional Center
• Full name: Marcus Valdane
• Job title: CEO
• Email address: mvaldane@valdanecompanies.com
• Cell phone number: +1.555.314.2287
• Office number +1.555.628.4410
• Office address: Larkfield Court 5, 4817 Vista Orilla, Calder Bay, WA.
• Website: www.valdanecompanies.com

Font styles to use
Serif
Sans Serif

Colors
ec1f27
ffffff
000000

Requirements
Must have
• • Logo for Valdane
• • Logo for Thornmere Regional Center
• - Use rounded corners
• (See .ai file included for logos)
Nice to have
• • Simple, elegant design
• • Aesthetically compatible with our website design (www.valdanecompanies.com)
• • Color palette including but not limited to white, black, and red (as per logos)
Should not have
• - Not too much red color
• - Do not stack both logos on top of each other

```html
<!DOCTYPE html>
<html lang="en">
<head>
<meta charset="utf-8">
<title>Valdane Companies Business Card</title>
<link rel="stylesheet" href="https://fonts.googleapis.com/css2?family=Cinzel:wght@600&family=Lato:wght@400&display=swap">
<style>
  :root {
    --stage: #1a1a1a;
    --card-front: #f3f3f3;
    --card-back: #fafafa;
    --ink: #2e2e2e;
    --ink-soft: #3a3a3a;
    --brand-red: #a3192e;
  }
  * { margin: 0; padding: 0; box-sizing: border-box; }
  html, body { width: 1200px; height: 900px; overflow: hidden; background: var(--stage); }
  .stage { position: relative; width: 1200px; height: 900px; }
  .card {
    position: absolute; top: 200px; width: 310px; height: 502px;
    box-shadow: 3px 4px 6px rgba(0,0,0,.6);
  }
  .card--front {
    left: 253px; background: var(--card-front);
    border-radius: 70px 0 70px 0;
  }
  .card--back {
    left: 627px; background: var(--card-back);
    border-radius: 0 70px 0 70px;
  }
  .brand {
    position: absolute; left: 0; right: 0; text-align: center;
    font-family: "Cinzel", serif; font-weight: 600;
  }
  .brand__name { display: block; line-height: 1; }
  .brand__sub { display: block; line-height: 1; }
  .brand--capital { top: 173px; color: var(--ink); }
  .brand--capital .brand__name { font-size: 46px; }
  .brand--capital .brand__sub { font-size: 13px; letter-spacing: 5.5px; margin-top: 10px; padding-left: 5px; }
  .brand--center { top: 268px; color: var(--brand-red); }
  .brand--center .brand__name { font-size: 40px; }
  .brand--center .brand__sub { font-size: 12px; letter-spacing: 5px; margin-top: 10px; padding-left: 5px; }
  .contact {
    position: absolute; left: 33px; top: 304px; color: var(--ink-soft);
    font-family: "Lato", sans-serif; font-size: 13.5px; line-height: 18px;
  }
  .contact__name {
    font-family: "Cinzel", serif; font-weight: 600; font-size: 19px;
    letter-spacing: .5px; color: var(--ink); line-height: 22px;
  }
  .contact__title { margin-bottom: 6px; }
  .contact__address { margin-bottom: 7px; }
  .contact__line { display: flex; align-items: center; gap: 4px; }
  .contact__line svg { width: 12px; height: 12px; fill: var(--ink); flex: none; }
  .site {
    position: absolute; left: 0; right: 0; top: 441px; text-align: center;
    font-family: "Lato", sans-serif; font-size: 13.5px; color: var(--ink);
  }
  .site__domain { color: var(--brand-red); }
</style>
</head>
<body>
<main class="stage">
  <section class="card card--front">
    <h1 class="brand brand--capital">
      <span class="brand__name">Valdane</span>
      <span class="brand__sub">CAPITAL</span>
    </h1>
    <div class="contact">
      <p class="contact__name">MARCUS VALDANE</p>
      <p class="contact__title">CEO</p>
      <p class="contact__address">Larkfield Court 5, 4817 Vista<br>Orilla, Calder Bay, WA.</p>
      <p class="contact__line">
        <svg viewBox="0 0 12 12"><path d="M1 3.5C1 2 3 1.5 6 1.5S11 2 11 3.5V5H8.5V4h-5v1H1z"/><path d="M3 5.5h6l1.5 4.5h-9z"/></svg>
        +1.555.314.2287
      </p>
      <p class="contact__line">
        <svg viewBox="0 0 12 12"><path d="M3 .5h6v11H3zM4 2v7h4V2z"/></svg>
        +1.555.628.4410
      </p>
      <p class="contact__line">
        <svg viewBox="0 0 12 12"><path d="M.5 2.5h11v7H.5zM1.5 3.5 6 7l4.5-3.5z"/></svg>
        mvaldane@valdanecompanies.com
      </p>
      <p class="contact__line">
        <svg viewBox="0 0 12 12"><circle cx="6" cy="6" r="5.5"/><path d="M4 3h2v2H4zM6.5 6.5h2.5v2h-2.5z" fill="#f3f3f3"/></svg>
        www.valdanecompanies.com
      </p>
    </div>
  </section>
  <section class="card card--back">
    <h2 class="brand brand--center">
      <span class="brand__name">Thornmere</span>
      <span class="brand__sub">REGIONAL CENTER</span>
    </h2>
    <p class="site">www.<span class="site__domain">valdanecompanies</span>.com</p>
  </section>
</main>
</body>
</html>
```